House flipping business web site needed

pinecrestholdingsgroup.example.
I am a residential developer in Northern NJ and I am looking for a fresh new updated website. I have an intro video about my company being made now. I don't update it very often but I want an easy format that I can add update photos to on projects I have worked on or homes I renovate for sale.

Target Market(s)

investors into my projects so a portfolio , people looking to sell their homes to me.

Industry/Entity Type

Real Estate Development

Number of Pages Required

4 page

Font styles to use
Serif

Colors
33b8a4
39a9d7
cadf82

Requirements
Must have
• space for an intro video about my company
• a portfolio with pictures and information about each project
• Markets we serve- Morris County, NJ
• My logo- already created
• SEO
• Yes I would like this to function over all platforms. Phone, computer, all platforms.
• history and background page
• I am looking for a completed page that I can upload to the site that hosts my website
Nice to have
• I want something creative, easy to navigate. modern.

```html
<!DOCTYPE html>
<html lang="en">
<head>
<meta charset="utf-8">
<title>Pinecrest Holdings Group</title>
<link rel="stylesheet" href="https://fonts.googleapis.com/css2?family=Lato:wght@300;400;700&family=Open+Sans:ital,wght@0,400;0,600;1,400&display=swap">
<style>
:root{
  --blue:#1aa9dc;
  --blue-light:#16b9ec;
  --ink:#2b2b2b;
  --text:#555;
  --header-bg:#f3f4f6;
  --footer-bg:#1f1f1f;
  --footer-text:#ddd;
  --white:#fff;
}
*{margin:0;padding:0;box-sizing:border-box}
html,body{width:711px;height:1200px;overflow:hidden}
body{position:relative;background:var(--white);font-family:"Open Sans",sans-serif;color:var(--text)}
.abs{position:absolute}
.site-header{left:0;top:0;width:711px;height:98px;background:var(--header-bg);border-top:2px solid var(--blue)}
.brand{left:78px;top:34px;display:flex;align-items:center;gap:7px;font-family:"Lato",sans-serif;font-size:15px;font-weight:700;color:#2a6fa8;letter-spacing:.5px}
.brand-mark{width:14px;height:14px;background:#2a6fa8;border-radius:50%}
.contact-label{font-size:6.5px;color:var(--blue);display:flex;align-items:center;gap:4px}
.contact-value{font-size:9px;color:var(--ink)}
.main-nav{top:73px;display:flex;font-size:6.5px;color:#333;text-transform:uppercase}
.main-nav a{position:absolute;white-space:nowrap;color:#333;text-decoration:none}
.main-nav a.active{color:var(--blue)}
.nav-indicator{left:378px;top:96px;width:24px;height:2px;background:var(--blue)}
.hero{left:0;top:98px;width:711px;height:278px;background:linear-gradient(180deg,#4a5560 0%,#3d4a3f 35%,#7a6a45 55%,#3a4a52 75%,#222c33 100%)}
.hero-title{left:78px;top:172px;font-family:"Lato",sans-serif;font-weight:400;font-size:22px;letter-spacing:1px;color:var(--white)}
.hero-text{left:79px;top:214px;width:250px;font-size:7.2px;line-height:14px;color:#eee}
.btn{display:flex;align-items:center;justify-content:center;background:var(--blue-light);color:var(--white);border-radius:2px;text-transform:uppercase}
.hero-btn{left:80px;top:259px;width:67px;height:23px;font-size:7px}
.dot{top:299px;width:5px;height:5px;border-radius:50%;background:#bbb}
.about-title{left:78px;top:411px;font-family:"Lato",sans-serif;font-size:17.5px;color:var(--ink)}
.about-sub{left:78px;top:444px;font-size:7px;font-style:italic;color:var(--blue)}
.about-copy{left:79px;top:467px;width:294px;font-size:5.6px;line-height:11.5px;color:#555;text-align:justify}
.about-copy p+p{margin-top:11px}
.about-btn{left:78px;top:547px;width:57px;height:24px;font-size:6.5px;text-transform:none}
.video-frame{left:391px;top:411px;width:244px;height:161px;border:1px solid #ddd;background:var(--white);padding:5px}
.video-area{width:100%;height:100%;background:linear-gradient(180deg,#cfe2ee 0%,#8aa85a 35%,#4d6a3a 55%,#5e7f8e 80%,#3f5560 100%);position:relative}
.play{left:97px;top:60px}
.help-band{left:0;top:630px;width:711px;height:212px;background:linear-gradient(180deg,#5d7b90 0%,#3e5a3a 30%,#8a8a80 45%,#3d5566 70%,#2a3e4c 100%)}
.help-title{left:0;top:687px;width:711px;text-align:center;font-family:"Lato",sans-serif;font-size:17px;color:var(--white)}
.help-text{left:130px;top:727px;width:451px;text-align:center;font-size:6.3px;line-height:13px;color:#eee}
.help-btn{left:298px;top:773px;width:115px;height:26px;border:2px solid var(--white);border-radius:14px;display:flex;align-items:center;justify-content:center;font-size:7.5px;font-weight:600;color:var(--white)}
.portfolio-title{left:0;top:864px;width:711px;text-align:center;font-family:"Lato",sans-serif;font-size:17px;letter-spacing:2.5px;color:var(--ink)}
.card{top:904px;width:132px;height:95px}
.card-feature{background:#3a3a3a;color:var(--white);text-align:center}
.card-feature h3{font-family:"Lato",sans-serif;font-weight:400;font-size:11.5px;margin-top:25px}
.card-feature p{font-size:6px;line-height:11px;margin-top:6px}
.arrow{top:937px}
.site-footer{left:0;top:1024px;width:711px;height:176px;background:var(--footer-bg);color:var(--footer-text)}
.footer-heading{top:1044px;font-family:"Lato",sans-serif;font-size:8.5px;color:var(--white);text-transform:uppercase}
.footer-line{font-size:5.8px;color:var(--footer-text);display:flex;align-items:flex-start;gap:6px}
.quick-links a{display:block;font-size:5.8px;color:var(--footer-text);text-decoration:none;line-height:12.3px}
.newsletter-note{left:365px;top:1067px;font-size:5.4px;color:#aaa}
.newsletter-input{left:365px;top:1086px;width:116px;height:21px;background:#3a3a3a;border:1px solid #555;font-size:5.8px;color:#ddd;padding:0 6px;display:flex;align-items:center}
.subscribe-btn{left:365px;top:1119px;width:51px;height:16px;font-size:5.2px}
.social{top:1067px;width:19px;height:19px;border:1px solid var(--white);border-radius:50%}
.footer-rule{left:79px;top:1164px;width:555px;height:1px;background:#444}
.copyright{left:0;top:1177px;width:711px;text-align:center;font-size:5.6px;color:#ccc}
</style>
</head>
<body>

<header class="abs site-header">
  <div class="abs brand" style="left:78px;top:32px"><span class="brand-mark"></span>Pinecrest Holdings Group</div>

  <div class="abs contact-label" style="left:447px;top:21px">
    <svg width="7" height="7" viewBox="0 0 10 10"><path d="M2 1l2 2-1 1.5c.8 1.5 1.5 2.2 3 3L7.5 6l2 2-1.5 1.5C4.5 9 1 5.5.5 2z" fill="none" stroke="#1aa9dc" stroke-width=".8"/></svg>CALL US</div>
  <div class="abs contact-value" style="left:447px;top:33px">862-555-0147</div>

  <div class="abs contact-label" style="left:549px;top:21px">
    <svg width="8" height="6" viewBox="0 0 10 7"><rect x=".5" y=".5" width="9" height="6" fill="none" stroke="#1aa9dc" stroke-width=".8"/><path d="M.5 .5L5 4l4.5-3.5" fill="none" stroke="#1aa9dc" stroke-width=".8"/></svg>EMAIL US</div>
  <div class="abs contact-value" style="left:549px;top:33px">info@pinecrestholdings.example</div>

  <nav class="abs main-nav">
    <a class="active" href="#" style="left:379px">Home</a>
    <a href="#" style="left:421px">About Us</a>
    <a href="#" style="left:476px">Services</a>
    <a href="#" style="left:530px">Portfolio</a>
    <a href="#" style="left:590px">Contact Us</a>
  </nav>
  <div class="abs nav-indicator" style="top:94px"></div>
</header>

<section>
  <div class="abs hero" role="img" aria-label="Mountain lake at sunrise with pine forest and granite cliffs"></div>
  <h1 class="abs hero-title">HOUSE FLIPPING BUSINESS</h1>
  <p class="abs hero-text">Lorem ipsum dolor sit amet, consectetur adipiscing elit, sed do eius-mod tempor incididunt ut labore</p>
  <a class="abs btn hero-btn">Read More</a>
  <span class="abs dot" style="left:79px;background:var(--blue)"></span>
  <span class="abs dot" style="left:90px"></span>
  <span class="abs dot" style="left:101px"></span>
</section>

<section>
  <h2 class="abs about-title">ABOUT PINECRESTHOLDINGSGROUP</h2>
  <p class="abs about-sub">We will help you get out of your unwanted home</p>
  <div class="abs about-copy">
    <p>Is a house in your neighborhood an eyesore? Is it vacant, boarded up and a hazard to the neighborhood? Please contact us and we can help transform that property into a beautiful home.<br>How we can help</p>
    <p>Do you need to sell your home fast to avoid foreclosure, have estate home you do not want to fix to put on the market, moving for a job and need your house sold fast. We can help. Contact us now.</p>
  </div>
  <a class="abs btn about-btn">Learn More</a>
  <div class="abs video-frame">
    <div class="video-area" role="img" aria-label="Company intro video: tree beside a calm forest lake">
      <svg class="abs play" width="34" height="34" viewBox="0 0 34 34"><circle cx="17" cy="17" r="15" fill="rgba(255,255,255,.35)" stroke="#444" stroke-width="2"/><path d="M13 10l11 7-11 7z" fill="#444"/></svg>
    </div>
  </div>
</section>

<section>
  <div class="abs help-band" role="img" aria-label="Alpine lake with pine trees and granite dome"></div>
  <h2 class="abs help-title">HOW WE CAN HELP</h2>
  <p class="abs help-text">Do you need to sell your home fast to avoid foreclosure, have estate home you do not want to fix to put on the market, moving for a job and need your house sold fast. We can help. Contact us now.</p>
  <a class="abs help-btn">LEARN MORE</a>
</section>

<section>
  <h2 class="abs portfolio-title">OUR PORTFOLIO</h2>
  <svg class="abs arrow" style="left:48px" width="16" height="30" viewBox="0 0 16 30"><path d="M14 1L2 15l12 14" fill="none" stroke="#555" stroke-width="1.2"/></svg>
  <div class="abs card card-feature" style="left:78px">
    <h3>HOUSE FLIPPING</h3>
    <p>Lorem ipsum dolor sit amet,<br>consectetur adipiscing</p>
  </div>
  <div class="abs card" style="left:219px;background:linear-gradient(180deg,#4f7a2e,#8a8a6a 60%,#5f8f2f)" role="img" aria-label="Small house among green trees"></div>
  <div class="abs card" style="left:360px;background:linear-gradient(180deg,#3f7fd0,#c9d2dc 50%,#7a6a5a)" role="img" aria-label="Home under renovation with building materials"></div>
  <div class="abs card" style="left:500px;background:linear-gradient(180deg,#3c86e0,#7a6a40 55%,#e6ecf2)" role="img" aria-label="Renovated house in winter"></div>
  <svg class="abs arrow" style="left:645px" width="16" height="30" viewBox="0 0 16 30"><path d="M2 1l12 14L2 29" fill="none" stroke="#555" stroke-width="1.2"/></svg>
</section>

<footer class="abs site-footer"></footer>
<h4 class="abs footer-heading" style="left:79px;top:1043px">Contact Us</h4>
<div class="abs footer-line" style="left:79px;top:1066px">
  <svg width="7" height="6" viewBox="0 0 10 8"><path d="M0 2h10v1.5H7.5v-1h-5v1H0zM2 4h6l1 4H1z" fill="#ddd"/></svg>0414 555 010</div>
<div class="abs footer-line" style="left:79px;top:1082px">
  <svg width="7" height="6" viewBox="0 0 10 8"><rect x="2" y="0" width="6" height="2" fill="#ddd"/><rect x="0" y="2.5" width="10" height="4" fill="#ddd"/><rect x="2" y="6" width="6" height="2" fill="#ddd"/></svg>0414 555 010</div>
<div class="abs footer-line" style="left:79px;top:1098px">
  <svg width="7" height="5" viewBox="0 0 10 7"><rect width="10" height="7" fill="#ddd"/><path d="M0 0l5 4 5-4" fill="none" stroke="#1f1f1f"/></svg><span style="text-decoration:underline">info@pinecrestholdings.example</span></div>
<div class="abs footer-line" style="left:79px;top:1114px;width:110px">
  <svg width="6" height="8" viewBox="0 0 6 8"><path d="M3 0a3 3 0 0 1 3 3c0 2-3 5-3 5S0 5 0 3a3 3 0 0 1 3-3z" fill="#ddd"/><circle cx="3" cy="3" r="1" fill="#1f1f1f"/></svg><span style="line-height:8px">#2868 Lorem ipsum dolor sit amet, consectetur</span></div>

<h4 class="abs footer-heading" style="left:246px;top:1045px">Quick Links</h4>
<nav class="abs quick-links" style="left:246px;top:1063px">
  <a href="#">Home</a><a href="#">About us</a><a href="#">services</a><a href="#">Portfolio</a><a href="#">COntact us</a>
</nav>

<h4 class="abs footer-heading" style="left:365px;top:1045px">Newsletter</h4>
<p class="abs newsletter-note">Sign Up for Our Newsletter &amp; Promotion</p>
<div class="abs newsletter-input">Enter Your email Id</div>
<a class="abs btn subscribe-btn">Subscribe</a>

<h4 class="abs footer-heading" style="left:529px;top:1045px">Follow Us</h4>
<span class="abs social" style="left:528px"></span>
<span class="abs social" style="left:550px"></span>
<span class="abs social" style="left:572px"></span>
<span class="abs social" style="left:594px"></span>
<span class="abs social" style="left:616px"></span>

<div class="abs footer-rule"></div>
<p class="abs copyright">Copyright 2016 © Pinecrest Holdings Group.</p>

</body>
</html>
```